"Tandem Mouthguards " Custom-made Mouthguard Business Website

We need an informational website for our mouthguard Business "Tandem Mouthguards". The logo is navy blue/lime green so want to have colour scheme that goes nicely with this - have uploaded our mouthguard flyer with some information we need to put into the website but I do have more information to put in there.

Target Market(s)

Sports clubs, sportspeople, parents and kids, schools

Industry/Entity Type

Dental, Custom-made Sports Mouthguards

Coding

Coded - Design and coding required

Number of Pages Required

5+ page

Font styles to use
Serif
Sans Serif

Colors
0054AA
0677BA
7BADD7
CADEEF
E8F1F8
0094D4
00A9DD
6FCCEA
C7EBF8
E9F6FB
00AB8E
00BBA5
67D7C9
C6EFE9
E9F9F6
59FF00
82FF00
B8FF75
E3FFCB
F4FFEA
FFF300
FFF600
FEFA6F
FFFEC7
FFFEE8
FFC000
F8CF3A
FAE287
FDF2CF
FEFAEE
F0912C
F2A743
F7CA91
FBE8D2
FDF5EE
EE7325
F08F49
F5BC92
FAE3D3
FDF4ED

Requirements
Must have
• I want drop down pages, not one scrolling page. Different pages for each heading . Content uploaded - We need a general home page with lots of pictures and info that I'll provide. A page each dedicated to 1) About Us 2) Why choose a custom mouthguard? 3) Gallery 4) Contact Us. Will need logos from "Velora"
Nice to have
• Mainly use greens and blues, but happy to pop in some yellow/oranges/red oranges if it looks good

```html
<!DOCTYPE html>
<html lang="en">
<head>
<meta charset="utf-8">
<title>Tandem Mouthguards – Custom-Made Sports Mouthguards</title>
<link href="https://fonts.googleapis.com/css2?family=Montserrat:wght@400;500;600;700&family=Nunito:wght@800;900&display=swap" rel="stylesheet">
<style>
:root{
  --navy:#002663;
  --navy-line:#3a5a96;
  --green:#2fc02a;
  --ink:#1e1e1e;
  --body:#333333;
  --white:#ffffff;
  --footer-blue:#2a9fd8;
}
*{box-sizing:border-box;margin:0;padding:0}
html,body{width:1200px;height:3937px;overflow:hidden}
body{position:relative;font-family:"Montserrat",sans-serif;color:var(--body);background:var(--white)}
.abs{position:absolute}
h1,h2,h3,.heading{font-family:"Nunito",sans-serif;font-weight:900}

/* hero */
.hero{left:0;top:0;width:1200px;height:642px;background:linear-gradient(120deg,#3f6b2c 0%,#5d8a3a 35%,#7a9a55 55%,#3d5f7a 78%,#2d4e86 100%)}
.brand{left:110px;top:18px;width:270px;color:var(--white);font-family:"Nunito",sans-serif;font-weight:900;display:flex;align-items:center;gap:10px}
.brand .dot{width:14px;height:14px;border-radius:50%;background:var(--green);flex:none}
.brand .name{display:flex;flex-direction:column;line-height:1}
.brand .line1{font-size:32px;letter-spacing:1px}
.brand .line2{font-size:17px;letter-spacing:.6px;margin-top:2px}
.nav{left:388px;top:21px;width:701px;height:46px;background:var(--navy);border-radius:23px;display:flex;align-items:center;padding-left:48px;gap:36px}
.nav a{color:var(--white);text-decoration:none;font-size:14px;font-weight:500;white-space:nowrap}
.nav a.active{color:var(--green)}
.hero-card{left:112px;top:142px;width:353px;height:395px;background:var(--navy);border-radius:22px 110px 22px 22px;padding:38px 26px 0 26px;color:var(--white)}
.hero-card h1{font-size:35px;line-height:38px;letter-spacing:.3px}
.hero-card .sub{font-family:"Nunito",sans-serif;font-weight:800;font-size:22px;line-height:26px;margin-top:18px}
.hero-card p{font-size:17.5px;line-height:25px;margin-top:14px}
.btn{display:inline-flex;align-items:center;justify-content:center;background:var(--green);color:var(--white);font-weight:700;font-size:16px;text-decoration:none;border-radius:2px}
.hero-card .btn{position:absolute;left:27px;top:309px;width:164px;height:49px}

/* about */
.about{left:0;top:642px;width:1200px;height:638px;background:linear-gradient(180deg,#d9efce 0%,#c9e4bd 55%,#c6dfc0 100%)}
.about h2{left:131px;top:121px;font-size:35px;color:var(--ink)}
.about p{left:410px;top:76px;width:700px;font-size:16.5px;line-height:26px;color:#2a2a2a}
.about-photo{left:112px;top:249px;width:319px;height:286px;border-radius:4px;background:linear-gradient(140deg,#3a5fa0,#1d2f57 60%,#4f77b0)}
.about-products{left:466px;top:252px;width:574px;height:268px;border-radius:40%/30%;background:radial-gradient(ellipse at 50% 60%,rgba(214,70,80,.45),rgba(90,140,210,.35) 50%,rgba(201,228,189,0) 72%)}

/* why */
.why h2{left:0;top:1350px;width:1200px;text-align:center;font-size:37px;color:var(--ink)}
.card{width:398px;height:257px;background:var(--navy);color:var(--white);padding:0 20px 0 41px;display:flex;align-items:center;font-family:"Nunito",sans-serif;font-weight:900;font-size:26px;line-height:42px;white-space:nowrap}
.card.l{padding-left:58px}
.card.tr{border-radius:14px 110px 14px 14px}
.card.tl{border-radius:110px 14px 14px 14px}
.card.br{border-radius:14px 14px 110px 14px}
.card.bl{border-radius:14px 14px 14px 110px}
.card.green{background:linear-gradient(135deg,#39b52c,#2aa526 50%,#3fbf22);border-radius:14px}
.card-photo{left:634px;top:1709px;width:398px;height:259px;border-radius:14px;background:linear-gradient(135deg,#8a6a4a,#cfc6bc 45%,#e9e5e0 60%,#7d2b35 80%,#a46a45)}
.gap-note{left:0;top:2445px;width:1200px;text-align:center;font-size:27px;line-height:41px;color:#3a3a3a}

/* process */
.process{left:0;top:2615px;width:1200px;height:925px;background:linear-gradient(100deg,#d9d7cf 0%,#e8e2d2 40%,#e5ddc6 70%,#d8d2c6 100%)}
.rule{left:112px;width:977px;height:1.5px;background:var(--navy-line)}
.step{left:365px;font-family:"Nunito",sans-serif;font-weight:800;font-size:23px;color:var(--ink)}
.step-text{left:613px;width:465px;font-size:16.5px;line-height:26px;color:#2a2a2a}
.ready{left:122px;top:3302px;font-weight:700;font-size:19px;color:var(--ink)}
.ready-note{left:122px;top:3332px;width:900px;font-size:16.5px;line-height:26px;color:#2a2a2a}
.process-btn{left:122px;top:3400px;width:164px;height:49px}

/* footer */
.footer-brand{left:112px;top:3660px;font-family:"Montserrat",sans-serif;font-weight:600;font-size:30px;color:var(--footer-blue);display:flex;align-items:center;gap:12px}
.footer-brand .sq{width:20px;height:20px;background:var(--footer-blue)}
.foot-rule{left:112px;width:977px;height:1.5px;background:var(--navy-line)}
.contact{left:122px;top:3772px;font-size:16px;line-height:27px;color:var(--ink)}
.contact strong{font-weight:700}
.address{left:482px;top:3775px;font-size:16px;line-height:26px;color:#2a2a2a}
.footer-btn{left:923px;top:3769px;width:164px;height:49px}
.copyright{left:122px;top:3874px;font-size:15px;color:#2a2a2a}
</style>
</head>
<body>

<header>
  <div class="abs hero" role="img" aria-label="Photo of two smiling kids in football jerseys holding a football, wearing coloured mouthguards"></div>
  <div class="abs brand"><span class="dot"></span><span class="name"><span class="line1">TANDEM</span><span class="line2">MOUTHGUARDS</span></span></div>
  <nav class="abs nav">
    <a class="active" href="#">Home</a>
    <a href="#">About Us</a>
    <a href="#">Our Mouthguards</a>
    <a href="#">Photo Gallery</a>
    <a href="#">FAQ</a>
    <a href="#">Contact Us</a>
  </nav>
  <section class="abs hero-card">
    <h1>TANDEM<br>MOUTHGUARDS</h1>
    <div class="sub">Custom-Made Sports<br>Mouthguards in Perth</div>
    <p>Protect your smile with<br>a comfortable,<br>professional fit.</p>
    <a class="btn" href="#">BOOK NOW</a>
  </section>
</header>

<section class="abs about">
  <h2 class="abs">About Us</h2>
  <p class="abs">My name is Elise, and I am a dental prosthetist with over 20 years of experience in the dental field. I hold a Diploma of Dental Technology and an Advanced Diploma of Dental Prosthetics, which I obtained at Westgate Institute of Technology in 2011. At Tandem Mouthguards (inside my Harbour Denture Care clinic), my work involves designing and making custom-fitted sports mouthguards for athletes of all ages.</p>
  <div class="abs about-photo" role="img" aria-label="Photo of a glittery dark blue custom mouthguard"></div>
  <div class="abs about-products" role="img" aria-label="Photo of an assortment of colourful custom mouthguards and cases"></div>
</section>

<section class="why">
  <h2 class="abs">Why Choose Us</h2>
  <div class="abs card tr" style="left:634px;top:1419px"><span>Professionally made<br>by a qualified dental<br>prosthetist</span></div>
  <div class="abs card l tl" style="left:191px;top:1552px"><span>Custom fit for<br>comfort, protection,<br>and durability</span></div>
  <div class="abs card-photo" role="img" aria-label="Photo of a maroon and white school mouthguard in its case"></div>
  <div class="abs card l green" style="left:191px;top:1844px"><span>Wide range of<br>colours and<br>designs</span></div>
  <div class="abs card br" style="left:634px;top:2001px"><span>Clinic and mobile<br>school/club visits<br>available</span></div>
  <div class="abs card l bl" style="left:191px;top:2135px"><span>Available for<br>kids, teens, and<br>adults</span></div>
  <p class="abs gap-note">Talk to us about our “gap free” mouthguards for eligible<br>private health insurance members.</p>
</section>

<section class="abs process" role="img" aria-label="Faded photo of kids holding a football, behind the process steps"></section>
<h2 class="abs heading" style="left:122px;top:2705px;font-size:36px;color:var(--ink)">The Process</h2>
<div class="abs rule" style="top:2771px"></div>
<div class="abs step" style="top:2814px">Step 1</div>
<p class="abs step-text" style="top:2806px">Book an appointment or mobile visit with<br>our dental prosthetist.</p>
<div class="abs rule" style="top:2888px"></div>
<div class="abs step" style="top:2953px">Step 2</div>
<p class="abs step-text" style="top:2925px">Impressions are taken of the mouth – this appointment will generally take around 15 minutes. You then get to choose your design (if you haven’t already!)</p>
<div class="abs rule" style="top:3031px"></div>
<div class="abs step" style="top:3074px">Step 3</div>
<p class="abs step-text" style="top:3067px">Mouthguard is made in-house in our laboratory by our prosthetist and technicians.</p>
<div class="abs rule" style="top:3150px"></div>
<div class="abs step" style="top:3192px">Step 4</div>
<p class="abs step-text" style="top:3186px">Fit and collection – you may either pick up from our clinic - or for sporting clubs or schools, we can have them packed and delivered to you.</p>
<div class="abs ready">Now you’re ready for game day!</div>
<p class="abs ready-note">Our turnaround time is generally 1-2 weeks,  however we may be able to accommodate quicker turnaround times. Contact us for more details</p>
<a class="abs btn process-btn" href="#">BOOK NOW</a>

<footer>
  <div class="abs footer-brand"><span class="sq"></span>HARBOUR DENTURE CARE</div>
  <div class="abs foot-rule" style="top:3741px"></div>
  <div class="abs contact"><strong>(08) 6100 2350</strong><br>info@tandemmouthguards.com.au</div>
  <div class="abs address">Unit 7, 14 Harbour Crescent, Eastvale,<br>Western Australia, 6000</div>
  <a class="abs btn footer-btn" href="#">BOOK NOW</a>
  <div class="abs foot-rule" style="top:3853px"></div>
  <div class="abs copyright">Copyright ©2025. All Rights Reserved</div>
</footer>

</body>
</html>
```